VOMRA Pty Ltd Business Card

Looking for a simple yet eye-catching double-sided business card design using my company logo on one side and contact details on the other.

Target Market(s)

Government

Industry/Entity Type

Communication Systems Engineering

Contact Information for Business Card

VOMRA Pty Ltd

Requirements
Nice to have
• Would be great to have a QR code so details can be scanned into contacts

```html
<!DOCTYPE html>
<html lang="en">
<head>
<meta charset="utf-8">
<title>VOMRA Pty Ltd Business Card</title>
<link rel="stylesheet" href="https://fonts.googleapis.com/css2?family=Mulish:wght@400;600;700&display=swap">
<style>
  :root {
    --backdrop: #e4e4e2;
    --card-dark: #262e35;
    --card-mid: #303a42;
    --card-light: #3b464f;
    --foil: rgba(176, 184, 191, 0.30);
    --foil-soft: rgba(150, 160, 168, 0.14);
    --ink: #ecebe7;
    --ink-soft: #d9d8d4;
    --rule: #d4d3cf;
  }
  * { box-sizing: border-box; margin: 0; padding: 0; }
  html, body {
    width: 1200px; height: 1200px; overflow: hidden;
    background: var(--backdrop);
    font-family: "Mulish", Arial, sans-serif;
  }
  .canvas { position: relative; width: 1200px; height: 1200px; }
  .card {
    position: absolute; left: 150px; width: 900px; height: 514px;
    background: linear-gradient(115deg, var(--card-dark) 0%, var(--card-mid) 55%, var(--card-light) 100%);
    overflow: hidden;
  }
  .card--front { top: 56px; }
  .card--back { top: 630px; color: var(--ink); }

  /* tonal area standing in for the repeating emblem pattern, silver foil upper left fading to blind emboss lower right */
  .front-pattern {
    position: absolute; inset: 0;
    background:
      linear-gradient(128deg, var(--foil) 0%, var(--foil-soft) 38%, rgba(0,0,0,0) 56%),
      linear-gradient(128deg, rgba(0,0,0,0) 56%, rgba(18,24,29,0.22) 100%);
  }
  .front-accent {
    position: absolute; left: 749px; top: 350px;
    width: 22px; height: 22px; border-radius: 50%;
    background: var(--ink);
  }

  .holder { position: absolute; left: 79px; top: 74px; }
  .holder__name { font-weight: 700; font-size: 40px; line-height: 1.1; letter-spacing: 0.2px; }
  .holder__title { font-weight: 400; font-size: 23px; color: var(--ink-soft); margin-top: 4px; }

  .divider { position: absolute; left: 79px; top: 173px; width: 735px; height: 2px; background: var(--rule); }

  .address {
    position: absolute; left: 79px; top: 256px;
    font-size: 23px; line-height: 32px; color: var(--ink-soft); font-style: normal;
  }
  .contacts { position: absolute; left: 79px; top: 332px; list-style: none; }
  .contacts li {
    display: flex; align-items: center; height: 34px;
    font-size: 23px; color: var(--ink-soft);
  }
  .contacts svg { width: 20px; height: 20px; margin-right: 12px; flex: none; }

  .brand {
    position: absolute; right: 86px; top: 350px;
    display: flex; align-items: center; gap: 16px;
  }
  .brand__dot { width: 22px; height: 22px; border-radius: 50%; background: var(--ink); }
  .brand__name { font-weight: 600; font-size: 66px; line-height: 1; color: var(--ink); letter-spacing: 1px; }
</style>
</head>
<body>
<main class="canvas">
  <section class="card card--front">
    <div class="front-pattern" role="img" aria-label="Repeating grid of the company emblem, silver foil in the upper left fading to tone-on-tone emboss on dark slate"></div>
    <span class="front-accent" aria-hidden="true"></span>
  </section>

  <section class="card card--back">
    <div class="holder">
      <h1 class="holder__name">Dalton Reeve</h1>
      <p class="holder__title">Founder &amp; Director</p>
    </div>
    <div class="divider"></div>
    <address class="address">
      47-49 Harlow Lane Westmere<br>
      NSW 2099 Australia
    </address>
    <ul class="contacts">
      <li>
        <svg viewBox="0 0 20 20" aria-hidden="true"><path d="M5 2.5l3 3.2-1.6 1.8c.9 2 2.4 3.6 4.4 4.6l1.8-1.6 3.2 3-1.6 2.6C9 15.8 4.2 11 2.5 5.2z" fill="var(--ink-soft)"/></svg>
        (402)-555-0147
      </li>
      <li>
        <svg viewBox="0 0 20 20" aria-hidden="true"><rect x="2" y="4.5" width="16" height="11" rx="1" fill="var(--ink-soft)"/><path d="M2.5 5l7.5 6 7.5-6" stroke="var(--card-mid)" stroke-width="1.6" fill="none"/></svg>
        admin@vomra.com.au
      </li>
      <li>
        <svg viewBox="0 0 20 20" aria-hidden="true"><g fill="none" stroke="var(--ink-soft)" stroke-width="1.6"><circle cx="10" cy="10" r="7.5"/><ellipse cx="10" cy="10" rx="3.2" ry="7.5"/><path d="M2.5 10h15"/></g></svg>
        www.vomra.com.au
      </li>
    </ul>
    <div class="brand">
      <span class="brand__dot"></span>
      <span class="brand__name">VOMRA</span>
    </div>
  </section>
</main>
</body>
</html>
```